Business card for marketing analytics company

Need a business card for new company. I have a logo already that I want to be built into the card and should use those colours

Company is called steered by tallies
Design must bring steered by tallies to life not be a card that could be for anyone with a logo put on it.

Like the front to be fairly clean and uncluttered bringing the logo out with a suitable design on the back of the card.

The logo represents a compass and business growth so those themes along with numbers, analytics , data are appropriate.
I'm often working with creative industries so also needs to reflect the creative side of analytics rather than be very corporate looking.

Target Market(s)

Ad agency, media agency, consumer goods clients

Industry/Entity Type

Market Research

Contact Information for Business Card

Needs to include name, title, email and phone number

Colors
f78f20
f68d4d
ec1f27

Requirements
Must have
• Must bring steered by tallies to life not be a card that could be for anyone with a logo put on it.
• Logo, Correct colours
• Like a design on the back that relates to company name
• Designs for both sides
Should not have
• Please do not just submit logo and a coloured card.
• It needs to have a design element to it
• No black background
• No clear cards - needs front & back

```html
<!DOCTYPE html>
<html lang="en">
<head>
<meta charset="utf-8">
<title>Steered by Tallies — Business Card</title>
<link href="https://fonts.googleapis.com/css2?family=PT+Sans:wght@400;700&display=swap" rel="stylesheet">
<style>
  :root {
    --backdrop: #e6e6e6;
    --card-white: #ffffff;
    --brand-orange: #f37325;
    --brand-red: #c8161e;
    --ink-grey: #4d555b;
    --text-grey: #555555;
    --chart-white: rgba(255, 255, 255, 0.38);
  }
  * { margin: 0; padding: 0; box-sizing: border-box; }
  html, body {
    width: 1200px;
    height: 987px;
    overflow: hidden;
    background: var(--backdrop);
    font-family: "PT Sans", sans-serif;
  }
  .canvas { position: relative; width: 1200px; height: 987px; }

  .card {
    position: absolute;
    left: 293px;
    width: 615px;
    height: 351px;
    box-shadow: 0 6px 18px rgba(0,0,0,0.18);
    overflow: hidden;
  }
  .card--front { top: 130px; background: var(--card-white); }
  .card--back  { top: 505px; background: var(--brand-orange); }

  /* Front: brand lockup */
  .brand-lockup {
    position: absolute;
    left: 50px;
    top: 50px;
    display: flex;
    align-items: center;
    gap: 18px;
  }
  .brand-dot {
    width: 58px; height: 58px;
    border-radius: 50%;
    border: 3px solid var(--brand-orange);
  }
  .brand-name {
    font-size: 28px;
    line-height: 1.05;
    font-weight: 400;
    color: var(--ink-grey);
  }

  /* Front: contact list */
  .contact-list {
    position: absolute;
    left: 50px;
    top: 238px;
    list-style: none;
  }
  .contact-item {
    display: flex;
    align-items: center;
    gap: 9px;
    height: 23.5px;
    font-size: 16px;
    color: var(--text-grey);
  }
  .contact-icon { width: 15px; height: 15px; flex: none; }

  /* Front: person */
  .person {
    position: absolute;
    right: 49px;
    top: 250px;
    text-align: right;
  }
  .person-name {
    font-size: 23px;
    font-weight: 700;
    color: var(--brand-orange);
    line-height: 1.1;
  }
  .person-title {
    font-size: 17px;
    color: var(--brand-red);
    line-height: 1.3;
  }
  .edge-tab {
    position: absolute;
    right: 0;
    top: 253px;
    width: 12px;
    height: 42px;
    background: var(--brand-orange);
  }

  /* Back */
  .growth-chart {
    position: absolute;
    left: 0;
    top: 0;
    width: 615px;
    height: 351px;
  }
  .back-lockup {
    position: absolute;
    left: 0; right: 0;
    top: 82px;
    display: flex;
    justify-content: center;
    align-items: center;
    gap: 18px;
  }
  .back-ring {
    width: 36px; height: 36px;
    border-radius: 50%;
    border: 3px solid var(--card-white);
  }
  .back-name {
    font-size: 42px;
    font-weight: 400;
    color: var(--card-white);
  }
  .back-web {
    position: absolute;
    left: 0; right: 0;
    top: 291px;
    text-align: center;
    font-size: 15px;
    letter-spacing: 6.5px;
    color: var(--card-white);
  }
</style>
</head>
<body>
<div class="canvas">

  <section class="card card--front" aria-label="Business card front">
    <div class="brand-lockup">
      <span class="brand-dot"></span>
      <span class="brand-name">Steered by<br>Tallies</span>
    </div>

    <ul class="contact-list">
      <li class="contact-item">
        <svg class="contact-icon" viewBox="0 0 16 16" aria-hidden="true">
          <path fill="#f37325" d="M3.5 1.5l2.3 2.6-1.2 1.8c.9 2 2.6 3.7 4.6 4.6l1.8-1.2 2.6 2.3-1.3 2.2C7.4 13.3 2.7 8.6 1.3 2.8z"/>
        </svg>
        555 201 4873
      </li>
      <li class="contact-item">
        <svg class="contact-icon" viewBox="0 0 16 16" aria-hidden="true">
          <rect x="1" y="3.5" width="14" height="9.5" fill="#f37325"/>
          <path d="M1.5 4l6.5 5 6.5-5" fill="none" stroke="#fff" stroke-width="1.2"/>
        </svg>
        alan@steeredbytally.com
      </li>
      <li class="contact-item">
        <svg class="contact-icon" viewBox="0 0 16 16" aria-hidden="true">
          <circle cx="8" cy="8" r="7" fill="#f37325"/>
          <path d="M1 8h14M8 1c-2.5 2-2.5 12 0 14M8 1c2.5 2 2.5 12 0 14" fill="none" stroke="#fff" stroke-width="1"/>
        </svg>
        www.steeredbytally.com
      </li>
    </ul>

    <div class="person">
      <p class="person-name">ALAN WHITMORE</p>
      <p class="person-title">CEO/Founder</p>
    </div>
    <span class="edge-tab"></span>
  </section>

  <section class="card card--back" aria-label="Business card back">
    <svg class="growth-chart" viewBox="0 0 615 351" aria-hidden="true">
      <g fill="var(--chart-white)">
        <rect x="187" y="232" width="16" height="18"/>
        <rect x="213" y="222" width="16" height="28"/>
        <rect x="239" y="226" width="16" height="24"/>
        <rect x="265" y="212" width="16" height="38"/>
        <rect x="291" y="204" width="16" height="46"/>
        <rect x="317" y="208" width="16" height="42"/>
        <rect x="343" y="192" width="16" height="58"/>
        <rect x="369" y="182" width="16" height="68"/>
        <rect x="395" y="170" width="16" height="80"/>
      </g>
      <line x1="175" y1="250.5" x2="440" y2="250.5" stroke="#ffffff" stroke-width="1.5"/>
    </svg>
    <div class="back-lockup">
      <span class="back-ring"></span>
      <span class="back-name">Steered by Tallies</span>
    </div>
    <p class="back-web">www.steeredbytally.com</p>
  </section>

</div>
</body>
</html>
```